Additional Benefits of Working for VELMAR

Please prepare an infographic on the additional benefits besides salary of working at VELMAR as detailed in the attached word document. Also attached is our logo in eps and our company design "Grounds". We are a Not For Profit company that finds jobs for unemployed people of government benefit payments

Brightway Market(s)

Attracting people to work for VELMAR. Making VELMAR an employer of choice.

Font styles to use
Sans Serif

Colors

Designer to choose colors to be used in the design.

Requirements
Must have
• be on 1 page
• have our logo
Nice to have
• Our Grounds design worked into it.
• Happy engaged employees
• Community engagement - we are a not for profit organisation
Should not have
• Discrimination, swearing,

```html
<!DOCTYPE html>
<html lang="en">
<head>
<meta charset="utf-8">
<title>8 Benefits Working With Us – VELMAR</title>
<link rel="stylesheet" href="https://fonts.googleapis.com/css2?family=Poppins:wght@400;600;700&display=swap">
<style>
  :root {
    --backdrop: #ececec;
    --paper: #ffffff;
    --ink: #1c1c1c;
    --teal: #2cc4b8;
    --gold: #f2c230;
    --lime: #9ad21e;
    --green: #3fe07a;
    --mint: #7ee0d8;
    --lavender: #a9b6e6;
    --plum: #4a1b3a;
    --rose: #c8335f;
    --red: #d23a4a;
    --orange: #f4742a;
    --slate: #5d6582;
    --navy: #1f4e86;
    --violet: #8b53c7;
    --lilac: #b88ae0;
    --line-olive: #a8c257;
    --line-sage: #7cc08a;
    --line-teal: #35c2b0;
    --line-yellow: #e4c33a;
  }
  * { box-sizing: border-box; margin: 0; padding: 0; }
  html, body { width: 1200px; height: 1200px; overflow: hidden; }
  body {
    background: var(--backdrop);
    font-family: "Poppins", sans-serif;
    color: var(--ink);
    position: relative;
  }
  .poster {
    position: absolute;
    left: 176px; top: 0;
    width: 848px; height: 1200px;
    background: var(--paper);
  }
  .poster-title {
    position: absolute;
    left: 49px; top: 38px;
    font-weight: 600;
    font-size: 57px;
    line-height: 60px;
    background: linear-gradient(120deg, var(--teal) 10%, var(--gold) 90%);
    -webkit-background-clip: text;
    background-clip: text;
    color: transparent;
  }
  .swirl { position: absolute; left: 0; top: 0; width: 848px; height: 1200px; }
  .swirl path { fill: none; stroke-width: 2.6; stroke-linecap: round; }
  .brand {
    position: absolute;
    left: 349px; top: 580px;
    width: 140px;
    display: flex; align-items: center; justify-content: center; gap: 6px;
    font-weight: 700; font-size: 28px; color: var(--ink);
  }
  .brand-dot { width: 12px; height: 12px; border-radius: 50%; background: var(--lime); }
  .benefit-card {
    position: absolute;
    width: 83px; height: 194px;
    border: 3px solid;
    border-radius: 14px;
    background: var(--paper);
    padding: 10px 7px;
    display: flex; flex-direction: column; justify-content: center; gap: 6px;
    font-size: 6.3px; line-height: 1.22;
  }
  .benefit-card p strong { font-weight: 700; }
  .benefit-card.dense {
    padding: 6px 6px;
    gap: 4px;
    font-size: 5.8px;
    line-height: 1.14;
  }
  .benefit-label {
    position: absolute;
    width: 180px;
    text-align: center;
    font-weight: 600;
    font-size: 17px;
    line-height: 19px;
  }
  .life { left: 381px; top: 155px; border-color: var(--gold); }
  .life strong { color: var(--teal); }
  .diversity { left: 240px; top: 300px; border-color: var(--plum); }
  .diversity strong { color: var(--rose); }
  .wellbeing { left: 520px; top: 300px; border-color: var(--lavender); }
  .wellbeing strong { color: var(--lavender); }
  .career { left: 645px; top: 506px; border-color: var(--lime); }
  .career strong { color: var(--green); }
  .recognition { left: 115px; top: 506px; border-color: var(--red); }
  .recognition strong { color: var(--rose); }
  .community { left: 240px; top: 712px; border-color: var(--orange); }
  .community strong { color: var(--orange); }
  .perks { left: 381px; top: 856px; border-color: var(--slate); }
  .perks strong { color: var(--navy); }
  .pay { left: 520px; top: 712px; border-color: var(--violet); }
  .pay strong { color: var(--violet); }
</style>
</head>
<body>
<main class="poster">
  <h1 class="poster-title">8 Benefits<br>Working<br>With US</h1>

  <svg class="swirl" viewBox="0 0 848 1200" aria-hidden="true">
    <path d="M409 349 Q472 453 497 563" stroke="var(--line-olive)"/>
    <path d="M320 456 Q414 472 447 518" stroke="var(--line-sage)"/>
    <path d="M570 493 Q533 649 461 679" stroke="var(--line-yellow)"/>
    <path d="M644 607 Q540 698 394 688" stroke="var(--line-yellow)"/>
    <path d="M199 596 Q360 480 447 519" stroke="var(--line-teal)"/>
    <path d="M272 710 Q300 560 381 524" stroke="var(--line-sage)"/>
    <path d="M433 855 Q350 740 337 577" stroke="var(--line-sage)"/>
    <path d="M520 751 Q420 730 344 644" stroke="var(--line-sage)"/>
  </svg>

  <div class="brand"><span class="brand-dot"></span>VELMAR</div>

  <h2 class="benefit-label" style="left:332px;top:120px;color:var(--teal)">Life Balance</h2>
  <section class="benefit-card life dense">
    <p><strong>VELMAR Day Leave</strong></p>
    <p>An extra day off at Christmas!</p>
    <p>Birthday Leave. A paid day off on your birthday</p>
    <p>A day off every month as Time in Lieu</p>
    <p><strong>4 weeks</strong> Annual Leave</p>
    <p>Generous Personal Leave</p>
    <p>Support for parental leave for the birth or adoption of a child</p>
    <p><strong>Flexible</strong> work arrangements</p>
  </section>

  <h2 class="benefit-label" style="left:192px;top:238px;color:var(--plum)">Diversity<br>&amp;<br>Inclusion</h2>
  <section class="benefit-card diversity">
    <p>An inclusive and <strong>diverse</strong> culture where different backgrounds, experiences and perspectives are <strong>valued</strong></p>
    <p>Gender diversity. Over <strong>50%</strong> of our workforce and our leaders are <strong>female.</strong></p>
  </section>

  <h2 class="benefit-label" style="left:472px;top:275px;color:var(--mint)">Wellbeing</h2>
  <section class="benefit-card wellbeing">
    <p>Up to <strong>$450</strong> per year to spend on Wellbeing services such as gym or yoga memberships</p>
    <p><strong>Free</strong> counselling services <strong>24x7</strong> via our Employee Assistance Program</p>
    <p>Discount private health insurance</p>
    <p>WHS policies which support a safe, inclusive work place</p>
  </section>

  <h2 class="benefit-label" style="left:597px;top:403px;color:var(--lime)">Career<br>Growth<br>&amp;<br>Professional<br>Development</h2>
  <section class="benefit-card career">
    <p>Ongoing internal training and development opportunities.</p>
    <p>External study support &amp; study leave</p>
    <p>Access to the tools and technology to do your job well</p>
    <p><strong>Career advancement</strong> opportunities</p>
    <p>Internal job vacancy listings</p>
  </section>

  <h2 class="benefit-label" style="left:67px;top:479px;color:var(--rose)">Recognition</h2>
  <section class="benefit-card recognition">
    <p>We <strong>celebrate</strong> our people for reaching service milestones</p>
    <p>Team &amp; individual recognition for high performance</p>
  </section>

  <section class="benefit-card community">
    <p>Team involvement in local charity and community events</p>
    <p>Participation in VELMAR's <strong>1000 Jobs</strong> in 100 days initiative</p>
    <p>Strong relationships and connection with Indigenous Communities in support of Indigenous Employment</p>
  </section>
  <h2 class="benefit-label" style="left:192px;top:913px;color:var(--orange)">Contributing<br>to Community</h2>

  <section class="benefit-card perks dense">
    <p>Discounted vouchers for:<br><strong>Harvest Mart, Greenleaf Grocers, Sonic Depot, Starlite Cinemas, Cellar Lane, ValuHub, Brightway, Outland Gear</strong><br>and many others via Paywise e-wallet</p>
    <p>A range of other employee discounts are also available, including access to discounted banking and finance, vehicle purchasing, leasing and hotel accommodation</p>
  </section>
  <h2 class="benefit-label" style="left:333px;top:1060px;color:var(--slate)">Benefits</h2>

  <section class="benefit-card pay">
    <p>Competitive salary</p>
    <p>Ability to salary package up to <strong>$15,900</strong> and reduce your tax. Package rent, home loans, child care and much more</p>
    <p>Salary package up to <strong>$2,650</strong> on meal entertainment and holiday accommodation</p>
  </section>
  <h2 class="benefit-label" style="left:472px;top:913px;color:var(--lilac)">Remuneration<br>&amp;<br>Salary Packaging</h2>
</main>
</body>
</html>
```